Logistics Website Design

See website https://tqfreightglobal.com for theme and color details. Need the site to be re-done and reflect some of the designs shown in this list here: https://pixelvane.com/tags/logistics-company-website

Target Market(s)

Logistics & Transportation

Industry/Entity Type

Logistics and Supply Chain

Coding

Number of Pages Required

5+ page

Requirements
Must have
• Colors must match theme of logo. Looking for a sleek, interactive design.

```html
<!DOCTYPE html>
<html lang="en">
<head>
<meta charset="utf-8">
<title>TQ Freight Global</title>
<link href="https://fonts.googleapis.com/css2?family=Bebas+Neue&family=Outfit:wght@300;400;500;600&display=swap" rel="stylesheet">
<style>
:root{
  --orange:#f9642f;
  --orange-soft:#fb8a5c;
  --ink:#111111;
  --text:#3d3d3d;
  --field:#f1f1f1;
  --blush:#fde6df;
  --footer:#160302;
  --white:#ffffff;
}
*{box-sizing:border-box;margin:0;padding:0}
html,body{width:1200px;height:3156px;overflow:hidden;background:var(--white)}
body{position:relative;font-family:"Outfit",sans-serif;color:var(--text)}
.abs{position:absolute}
.display{font-family:"Bebas Neue",sans-serif;color:var(--ink);font-weight:400;line-height:1}
.btn{position:absolute;display:flex;align-items:center;justify-content:center;background:linear-gradient(90deg,var(--orange),var(--orange-soft));color:var(--white);font-size:11px;font-weight:600;text-transform:uppercase;border-radius:5px}

/* header */
.site-header{position:absolute;left:0;top:0;width:1200px;height:77px;background:var(--white);z-index:3}
.brand{position:absolute;left:114px;top:18px;display:flex;align-items:center;gap:10px;z-index:4}
.brand-dot{width:40px;height:40px;border-radius:50%;background:var(--orange)}
.brand-name{font-family:"Outfit",sans-serif;font-weight:600;font-size:17px;color:var(--ink);letter-spacing:.5px}
.main-nav{position:absolute;top:0;height:77px;left:0;width:1200px}
.main-nav a{position:absolute;top:32px;font-size:11px;font-weight:500;color:var(--ink);text-decoration:none;text-transform:uppercase}
.home-icon{position:absolute;left:501px;top:30px}
.contact-btn{left:960px;top:17px;width:127px;height:43px}

/* hero */
.hero{position:absolute;left:0;top:77px;width:1200px;height:625px;background:linear-gradient(180deg,#d9763b 0%,#e89548 30%,#9b4a24 62%,#3d2a20 100%)}
.hero-truck{position:absolute;left:600px;top:80px;width:600px;height:520px;background:linear-gradient(160deg,#c8c3c0 0%,#b04a22 40%,#3a2a25 100%);border-radius:6px 0 0 0;opacity:.85}
.hero-title{position:absolute;left:113px;top:170px;font-size:66px;color:var(--white);width:500px;line-height:.9}
.hero-sub{position:absolute;left:113px;top:364px;font-family:"Bebas Neue",sans-serif;font-size:19px;color:var(--white)}
.hero-btn{left:113px;top:406px;width:159px;height:43px}
.slider{position:absolute;left:510px;top:577px;display:flex;align-items:center;gap:10px;color:var(--white);font-size:14px}
.slider .dash{width:24px;height:1px;background:var(--white)}

/* marquee */
.ticker{position:absolute;left:0;top:735px;width:1200px;height:44px;display:flex;align-items:center;gap:26px;white-space:nowrap;padding-left:5px}
.ticker span{font-family:"Bebas Neue",sans-serif;font-size:44px;color:transparent;-webkit-text-stroke:1px #555}
.ticker i{font-style:normal;font-size:30px}

/* about */
.about-media{position:absolute;left:163px;top:864px;width:413px;height:256px;border-radius:14px;background:linear-gradient(180deg,#7aa8b8 0%,#c6a59a 40%,#1d6e86 70%,#0d3f55 100%)}
.about-title{position:absolute;left:621px;top:885px;font-size:45px}
.about-text{position:absolute;left:621px;top:984px;width:420px;font-size:12.6px;line-height:18.7px;font-weight:300;color:#444}

/* services */
.section-title{position:absolute;left:0;width:1200px;text-align:center}
.service-card{position:absolute;top:1271px;width:282px;height:305px}
.service-photo{position:absolute;left:0;top:0;width:282px;height:252px;border-radius:14px}
.service-info{position:absolute;left:24px;top:213px;width:258px;height:92px;background:#f5f5f5;border-radius:12px 0 12px 12px}
.service-info h3{position:absolute;left:27px;top:30px;font-size:22px;line-height:26px;font-family:"Bebas Neue",sans-serif;font-weight:400;color:var(--ink)}
.service-badge{position:absolute;left:215px;top:190px;width:67px;height:45px;background:var(--orange);border-radius:10px 0 0 0;display:flex;align-items:center;justify-content:center}
.service-arrow{position:absolute;left:211px;top:50px;width:32px;height:32px;background:var(--white);border-radius:5px;display:flex;align-items:center;justify-content:center}
.more-btn{left:516px;top:1614px;width:168px;height:43px}

/* story */
.story{position:absolute;left:0;top:1745px;width:1200px;height:1025px;background:linear-gradient(180deg,var(--blush) 0%,#fef3ef 45%,var(--white) 70%)}
.story-title{position:absolute;left:123px;top:104px;font-size:45px}
.story-text{position:absolute;left:123px;top:156px;width:425px;font-size:12.6px;line-height:18.7px;font-weight:300;color:#444}
.story-text p+p{margin-top:14px}
.story-btn{left:123px;top:420px;width:122px;height:43px}
.story-media{position:absolute;left:651px;top:74px;width:425px;height:420px;border-radius:14px;background:linear-gradient(180deg,#6e9cc6 0%,#a6b58c 35%,#c46a3a 60%,#4a4a48 100%)}

/* contact */
.contact-title{top:2320px;font-size:46px}
.contact-sub{top:2380px;font-size:12.5px;color:#444;font-weight:300}
.field{position:absolute;background:var(--field);border-radius:4px;display:flex;align-items:center;gap:8px;padding-left:18px;font-size:10.5px;color:#555;text-transform:uppercase}
.field.msg{align-items:flex-start;padding-top:14px}
.submit{position:absolute;left:297px;top:2630px;width:606px;height:46px;border-radius:5px;background:linear-gradient(90deg,var(--orange),var(--orange-soft));color:var(--white);font-size:12px;font-weight:600;display:flex;align-items:center;justify-content:center}
.submit svg{position:absolute;right:22px;top:15px}

/* footer */
.site-footer{position:absolute;left:0;top:2770px;width:1200px;height:386px;background:var(--footer)}
.footer-brand{position:absolute;left:0;width:1200px;top:110px;display:flex;justify-content:center;align-items:center;gap:14px}
.footer-brand .brand-dot{width:56px;height:56px}
.footer-brand .brand-name{color:var(--white);font-size:30px}
.footer-nav a{position:absolute;top:268px;transform:translateX(-50%);font-size:12.5px;color:var(--white);text-decoration:none;text-transform:uppercase}
.footer-rule{position:absolute;left:113px;top:337px;width:974px;height:1px;background:#5a4a48}
.copyright{position:absolute;left:0;width:1200px;top:355px;text-align:center;font-size:12px;color:var(--white)}
.chat{position:absolute;left:1105px;top:3070px;width:73px;height:73px;border-radius:50%;background:var(--white);display:flex;align-items:center;justify-content:center;box-shadow:0 2px 8px rgba(0,0,0,.3)}
</style>
</head>
<body>

<header class="site-header">
  <div class="brand"><span class="brand-dot"></span><span class="brand-name">TQ FREIGHT GLOBAL</span></div>
  <nav class="main-nav">
    <svg class="home-icon" width="15" height="14" viewBox="0 0 15 14"><path d="M7.5 1 1 7h2v6h3.5V9h2v4H12V7h2z" fill="#f9642f"/></svg>
    <a style="left:540px">Services</a>
    <a style="left:634px">Industries</a>
    <a style="left:739px">Request a Quote</a>
    <a style="left:882px">About Us</a>
  </nav>
  <div class="btn contact-btn">Contact Us</div>
</header>

<section class="hero">
  <div class="hero-truck" role="img" aria-label="Orange semi truck on a highway at sunset"></div>
  <h1 class="display hero-title">Delivering strength in every mile secure</h1>
  <p class="hero-sub">And reliable transportation for all your cargo needs.</p>
  <div class="btn hero-btn">Request a Quote</div>
  <div class="slider">
    <svg width="10" height="12" viewBox="0 0 10 12"><path d="M7 1 2 6l5 5" stroke="#fff" stroke-width="2" fill="none"/></svg>
    <span>01</span><span class="dash"></span><span>02</span><span class="dash"></span><span>03</span>
    <svg width="10" height="12" viewBox="0 0 10 12"><path d="m3 1 5 5-5 5" stroke="#fff" stroke-width="2" fill="none"/></svg>
  </div>
</section>

<div class="ticker">
  <span>Supply Chain</span><i>🚢</i><span>Warehousing</span><i>✈️</i><span>Global Shipping</span><i>🚛</i><span>Fast Delivery</span>
</div>

<section class="about">
  <div class="about-media" role="img" aria-label="Container ship loaded with cargo at sea"></div>
  <h2 class="display about-title">Keeping your<br>supply chain moving</h2>
  <p class="about-text">We deliver a comprehensive range of open-deck and specialized transportation services—including flatbed, step deck, heavy haul, and over-dimensional freight solutions. Backed by years of experience, a trusted nationwide carrier network, and a strong safety-first culture, we provide reliable, adaptable logistics support built around the unique requirements of every load.</p>
</section>

<section class="services">
  <h2 class="display section-title" style="top:1205px;font-size:45px">Our Services</h2>

  <article class="service-card" style="left:157px">
    <div class="service-photo" role="img" aria-label="Worker in safety vest checking a tablet beside a truck" style="background:linear-gradient(135deg,#6b5b52,#a38d6f 50%,#7a3d2c)"></div>
    <div class="service-badge"><svg width="34" height="24" viewBox="0 0 34 24" fill="none" stroke="#fff" stroke-width="2"><rect x="2" y="3" width="19" height="14" rx="2"/><path d="M21 8h6l5 5v4h-11z"/><circle cx="9" cy="19" r="3"/><circle cx="26" cy="19" r="3"/></svg></div>
    <div class="service-info"><h3>Flatbed<br>Transportation</h3><div class="service-arrow"><svg width="12" height="12" viewBox="0 0 12 12"><path d="M2 10 10 2M4 2h6v6" stroke="#222" fill="none"/></svg></div></div>
  </article>

  <article class="service-card" style="left:458px">
    <div class="service-photo" role="img" aria-label="Worker in blue cap walking between container stacks with a tablet" style="background:linear-gradient(135deg,#3b4048,#9a9ea2 50%,#2d4f8a)"></div>
    <div class="service-badge"><svg width="34" height="24" viewBox="0 0 34 24" fill="none" stroke="#fff" stroke-width="2"><path d="M3 12h26l3-2-3-2H3zM12 8 8 2h4l7 6M12 16l-4 6h4l7-6"/></svg></div>
    <div class="service-info"><h3>Step Deck<br>Transportation</h3><div class="service-arrow"><svg width="12" height="12" viewBox="0 0 12 12"><path d="M2 10 10 2M4 2h6v6" stroke="#222" fill="none"/></svg></div></div>
  </article>

  <article class="service-card" style="left:760px">
    <div class="service-photo" role="img" aria-label="Dispatcher with clipboard and radio beside a white van" style="background:linear-gradient(135deg,#cfd4d8,#5a7ca3 50%,#b2302a)"></div>
    <div class="service-badge"><svg width="34" height="24" viewBox="0 0 34 24" fill="none" stroke="#fff" stroke-width="2"><rect x="2" y="3" width="19" height="14" rx="2"/><path d="M21 8h6l5 5v4h-11z"/><circle cx="9" cy="19" r="3"/><circle cx="26" cy="19" r="3"/></svg></div>
    <div class="service-info"><h3>Dry Van<br>Transportation</h3><div class="service-arrow"><svg width="12" height="12" viewBox="0 0 12 12"><path d="M2 10 10 2M4 2h6v6" stroke="#222" fill="none"/></svg></div></div>
  </article>

  <div class="btn more-btn">View More Service</div>
</section>

<section class="story">
  <h2 class="display story-title">Our Story</h2>
  <div class="story-text">
    <p>TQ Freight Global™ was born out of real-world experience in the fitness equipment industry. What started as a company shipping strength equipment, cardio machines, and training gear to gyms, schools, and commercial facilities quickly evolved into something bigger. As order volume grew and supply chains became more complex, the team developed deep expertise in coordinating freight, managing deliveries, and navigating the challenges of large-scale equipment transportation. That hands-on experience laid the foundation for what would eventually become a full-service logistics operation.</p>
    <p>Recognizing the opportunity to build a more efficient &amp; reliable transportation network, TQ Freight expanded beyond fitness equipment and began offering logistics.</p>
  </div>
  <div class="btn story-btn">Read More</div>
  <div class="story-media" role="img" aria-label="Orange truck driving on a coastal highway"></div>
</section>

<section class="contact">
  <h2 class="display section-title contact-title">Let's move your business forward</h2>
  <p class="section-title contact-sub">Let's discuss your logistics needs and how we can help your business thrive</p>
  <div class="field" style="left:297px;top:2427px;width:298px;height:41px"><svg width="10" height="10" viewBox="0 0 10 10"><circle cx="5" cy="3" r="2.5" fill="#444"/><path d="M0 10a5 4 0 0 1 10 0z" fill="#444"/></svg>First Name</div>
  <div class="field" style="left:605px;top:2427px;width:298px;height:41px"><svg width="10" height="10" viewBox="0 0 10 10"><circle cx="5" cy="3" r="2.5" fill="#444"/><path d="M0 10a5 4 0 0 1 10 0z" fill="#444"/></svg>Last Name</div>
  <div class="field" style="left:297px;top:2476px;width:298px;height:42px"><svg width="11" height="9" viewBox="0 0 11 9"><rect width="11" height="9" rx="1" fill="#444"/><path d="m0 1 5.5 4L11 1" stroke="#f1f1f1" fill="none"/></svg>Email</div>
  <div class="field" style="left:605px;top:2476px;width:298px;height:42px"><svg width="10" height="10" viewBox="0 0 10 10"><path d="M2 0h2l1 3-1.5 1a6 6 0 0 0 2.5 2.5L7 5l3 1v2c0 1-1 2-2 2A8 8 0 0 1 0 2c0-1 1-2 2-2z" fill="#444"/></svg>Phone Number</div>
  <div class="field msg" style="left:297px;top:2526px;width:606px;height:92px"><svg width="11" height="10" viewBox="0 0 11 10"><path d="M1 1h9v6H4l-3 3z" fill="#444"/></svg>Message</div>
  <div class="submit">SUBMIT NOW<svg width="16" height="16" viewBox="0 0 16 16"><path d="M1 7 15 1 11 15 8 9z" fill="#fff"/></svg></div>
</section>

<footer class="site-footer">
  <div class="footer-brand"><span class="brand-dot"></span><span class="brand-name">TQ FREIGHT GLOBAL</span></div>
  <nav class="footer-nav">
    <a style="left:283px">Home</a>
    <a style="left:381px">Services</a>
    <a style="left:495px">Industries</a>
    <a style="left:637px">Request a Quote</a>
    <a style="left:776px">About Us</a>
    <a style="left:895px">Contact Us</a>
  </nav>
  <div class="footer-rule"></div>
  <p class="copyright">© 2026. An independent agent of Bellmark Carriers LLC.</p>
</footer>

<div class="chat"><svg width="38" height="32" viewBox="0 0 38 32"><path d="M4 2h22a3 3 0 0 1 3 3v12a3 3 0 0 1-3 3H12l-7 6v-6H4a3 3 0 0 1-3-3V5a3 3 0 0 1 3-3z" fill="#f9642f"/><path d="M31 9h3a3 3 0 0 1 3 3v10a3 3 0 0 1-3 3h-1v5l-6-5H16" fill="none" stroke="#f9642f" stroke-width="2"/><circle cx="9" cy="11" r="2" fill="#fff"/><circle cx="15" cy="11" r="2" fill="#fff"/><circle cx="21" cy="11" r="2" fill="#fff"/></svg></div>

</body>
</html>
```